Executive recruiting firm in need of business card design

Executive recruiting firm looking for a sleek, classy and modern business card design; card itself will be square shape, rounded edges and soft touch paper, our colors are dark blues in the navy color scale, silvers and grays. Reference our website for a better idea of our company's feel and goals at Tarvex-Up.com - our company message is "Employee Engagement Begins at Recruitment" this should be on the card

```html
<!DOCTYPE html>
<html lang="en">
<head>
<meta charset="utf-8">
<title>Tarvex-Up Business Card</title>
<link rel="stylesheet" href="https://fonts.googleapis.com/css2?family=Barlow:wght@300;400;500;600&display=swap">
<style>
  :root {
    --page: #e6e6e6;
    --navy: #141848;
    --navy-deep: #10143c;
    --navy-soft: #1d2358;
    --white: #ffffff;
    --silver: #c9ccd8;
    --panel: rgba(255, 255, 255, 0.15);
  }
  * { margin: 0; padding: 0; box-sizing: border-box; }
  html, body {
    width: 1200px;
    height: 624px;
    overflow: hidden;
    background: var(--page);
    font-family: "Barlow", Arial, sans-serif;
  }
  .canvas {
    position: relative;
    width: 1200px;
    height: 624px;
  }
  .card {
    position: absolute;
    top: 152px;
    width: 320px;
    height: 320px;
    border-radius: 18px;
    overflow: hidden;
    background: var(--navy);
  }
  .card--front { left: 218px; }
  .card--back { left: 661px; }
  .card__photo {
    position: absolute;
    inset: 0;
    background:
      radial-gradient(ellipse 22% 45% at 48% 70%, var(--navy-deep) 0%, transparent 100%),
      linear-gradient(180deg, var(--navy) 0%, var(--navy-soft) 70%, var(--navy) 100%);
  }
  .brand {
    position: absolute;
    left: 0;
    right: 0;
    top: 160px;
    transform: translateY(-50%);
    text-align: center;
    color: var(--white);
  }
  .brand__name {
    display: block;
    font-weight: 300;
    font-size: 38px;
    letter-spacing: 4px;
    line-height: 1;
  }
  .brand__tagline {
    display: block;
    font-weight: 300;
    font-size: 8px;
    letter-spacing: 3px;
    margin-top: 6px;
  }
  .card__message {
    position: absolute;
    left: 0;
    right: 0;
    bottom: 26px;
    text-align: center;
    color: var(--silver);
    font-weight: 400;
    font-size: 10px;
    letter-spacing: 1.2px;
  }
  .contact-panel {
    position: absolute;
    left: 45px;
    top: 45px;
    width: 230px;
    height: 230px;
    border-radius: 50%;
    background: var(--panel);
    color: var(--white);
    text-align: center;
    padding-top: 40px;
  }
  .contact-panel__name {
    font-weight: 600;
    font-size: 18.5px;
    line-height: 1.2;
  }
  .contact-panel__role {
    font-weight: 400;
    font-size: 11.5px;
    margin-top: 2px;
  }
  .contact-panel__lines {
    margin-top: 17px;
    font-size: 12px;
    line-height: 17.5px;
  }
  .contact-panel__address {
    margin-top: 8px;
    font-size: 12px;
    line-height: 16px;
  }
</style>
</head>
<body>
<main class="canvas">
  <section class="card card--front">
    <div class="card__photo" role="img" aria-label="Dim navy-toned photo of a businessman standing by a tall office window"></div>
    <div class="brand">
      <span class="brand__name">TARVEX UP</span>
      <span class="brand__tagline">talent acquisition</span>
    </div>
    <p class="card__message">Employee Engagement Begins at Recruitment</p>
  </section>

  <section class="card card--back">
    <div class="card__photo" role="img" aria-label="Dim navy-toned photo of a businessman standing by a tall office window"></div>
    <div class="contact-panel">
      <p class="contact-panel__name">Employee Name</p>
      <p class="contact-panel__role">Managing Director</p>
      <p class="contact-panel__lines">
        00-1234-1234-55<br>
        employee@tarvex-up.com<br>
        www.tarvex-up.com
      </p>
      <p class="contact-panel__address">
        482 Linden Crest Ave, Marlow Bay,<br>
        CA 90210, USA
      </p>
    </div>
  </section>
</main>
</body>
</html>
```